Business Card Design for Training Business

Clear Path Coaching is a new business that delivers training and other services with a focus on topics related to mental health and wellbeing, for example, Wellmind Response Course, Resilience etc. We have a strong focus on evidence-based psychology and neuroscience. I have a logo which I will upload with the brief, so please consider colours that work well with the logo.
Target Market(s)
Adults, workplaces (particularly government and not-for-profits)
Industry/Entity Type
Business
Contact Information for Business Card
Head Strong TrainingSamantha SellwoodDirector0438 770 850sam@headstrongtraining.com.auwww.headstrongtraining.com.au

```html
<!DOCTYPE html>
<html lang="en">
<head>
<meta charset="utf-8">
<title>Clear Path Coaching – Business Card</title>
<link rel="stylesheet" href="https://fonts.googleapis.com/css2?family=Lato:wght@400;700&family=Raleway:wght@300&display=swap">
<style>
  :root {
    --page-bg: #2e2e2e;
    --card-light: #fbfbfb;
    --card-mid: #e9e8e6;
    --card-shade: #d9d8d5;
    --teal: #3fb7bf;
    --ink: #5a5a5a;
    --ink-dark: #3d3d3d;
  }
  * { margin: 0; padding: 0; box-sizing: border-box; }
  html, body {
    width: 1200px;
    height: 857px;
    overflow: hidden;
    background: var(--page-bg);
  }
  .stage {
    width: 1200px;
    height: 857px;
    display: flex;
    align-items: center;
    justify-content: center;
  }
  .card {
    position: relative;
    width: 1050px;
    height: 600px;
    overflow: hidden;
    box-shadow: 0 18px 40px rgba(0,0,0,0.45);
  }
  .card__texture {
    position: absolute;
    inset: 0;
    background:
      radial-gradient(ellipse at 30% 30%, var(--card-light) 0%, rgba(255,255,255,0) 55%),
      radial-gradient(ellipse at 80% 75%, var(--card-light) 0%, rgba(255,255,255,0) 50%),
      linear-gradient(135deg, var(--card-mid) 0%, var(--card-light) 45%, var(--card-shade) 100%);
  }
  .brand {
    position: absolute;
    left: 80px;
    top: 120px;
    width: 470px;
    display: flex;
    flex-direction: column;
    align-items: center;
  }
  .brand__mark {
    width: 150px;
    height: 150px;
    margin-bottom: 40px;
  }
  .brand__name {
    font-family: 'Raleway', sans-serif;
    font-weight: 300;
    color: var(--ink);
    text-align: center;
    line-height: 1.1;
  }
  .brand__name-main {
    display: block;
    font-size: 50px;
    letter-spacing: 5px;
  }
  .brand__name-sub {
    display: block;
    font-size: 22px;
    letter-spacing: 12px;
    margin-top: 6px;
  }
  .person {
    position: absolute;
    left: 600px;
    top: 100px;
  }
  .person__name {
    font-family: 'Lato', sans-serif;
    font-weight: 400;
    font-size: 27px;
    letter-spacing: 0.5px;
    text-transform: uppercase;
    color: var(--teal);
  }
  .person__role {
    font-family: 'Lato', sans-serif;
    font-weight: 400;
    font-size: 24px;
    color: var(--ink);
    margin-top: 6px;
  }
  .contact {
    position: absolute;
    left: 600px;
    top: 290px;
    list-style: none;
  }
  .contact__item {
    display: flex;
    align-items: center;
    gap: 16px;
    margin-bottom: 18px;
    font-family: 'Lato', sans-serif;
    font-weight: 700;
    font-size: 22px;
    color: var(--ink-dark);
  }
  .contact__icon {
    width: 24px;
    height: 24px;
    flex: none;
  }
</style>
</head>
<body>
<main class="stage">
  <section class="card">
    <div class="card__texture" role="img" aria-label="Soft pale grey faceted low-poly background texture"></div>

    <div class="brand">
      <svg class="brand__mark" viewBox="0 0 150 150" aria-hidden="true">
        <circle cx="75" cy="75" r="70" fill="none" stroke="var(--teal)" stroke-width="3"/>
      </svg>
      <p class="brand__name">
        <span class="brand__name-main">CLEAR PATH</span>
        <span class="brand__name-sub">COACHING</span>
      </p>
    </div>

    <div class="person">
      <h1 class="person__name">Rebecca Tanfield</h1>
      <p class="person__role">Director</p>
    </div>

    <ul class="contact">
      <li class="contact__item">
        <svg class="contact__icon" viewBox="0 0 24 24" aria-hidden="true">
          <path d="M3 9c0-3 4-5 9-5s9 2 9 5l-1 2h-4l-1-2.5H9L8 11H4z" fill="var(--teal)"/>
          <rect x="5" y="12" width="14" height="9" rx="1.5" fill="var(--teal)"/>
          <circle cx="12" cy="16.5" r="2.2" fill="var(--card-light)"/>
        </svg>
        <span>0491 362 517</span>
      </li>
      <li class="contact__item">
        <svg class="contact__icon" viewBox="0 0 24 24" aria-hidden="true">
          <rect x="2" y="5" width="20" height="14" rx="1" fill="var(--teal)"/>
          <path d="M2.5 5.5 12 13l9.5-7.5" fill="none" stroke="var(--card-light)" stroke-width="1.6"/>
        </svg>
        <span>bec@clearpathcoaching.example.au</span>
      </li>
      <li class="contact__item">
        <svg class="contact__icon" viewBox="0 0 24 24" aria-hidden="true">
          <g fill="none" stroke="var(--teal)" stroke-width="2.6" stroke-linecap="round">
            <path d="M10 14a4 4 0 0 1 0-5.6l3-3a4 4 0 0 1 5.6 5.6l-1.5 1.5"/>
            <path d="M14 10a4 4 0 0 1 0 5.6l-3 3a4 4 0 0 1-5.6-5.6l1.5-1.5"/>
          </g>
        </svg>
        <span>www.clearpathcoaching.example.au</span>
      </li>
    </ul>
  </section>
</main>
</body>
</html>
```